yourCartly - a stylish trolley for apartments

We neede a simple website to sell our Trolley, for apartment use.
The colour theme is red, blask & white. Our logo is attached and this needs to be on the Home page.
The website only needs a Home Page plus 4 other pges.
In the attachment you will find a site map.

You can check out the following two sites to see what I like:
www.plainvexo.com/design-showcase-inspiration/minimalist-portfolio-website/
www.brightquillor.com/inspiration/40-beautiful-web-design-portfolios/ in this site especially
Dario Penhaske
G K Maker
Nine 17 Works
Marcus Bell

And especially Lamp - I ike the simpicity of the site esp as we are only selling one product

Target Market(s)

Apartment dwellers

Industry/Entity Type

Apartment

Requirements
Must have
• This website must have 4 pages.
We need Zorva, Pelicoin and Quidnet portals.
Order Form for Trolley
Payment form.

```html
<!DOCTYPE html>
<html lang="en">
<head>
<meta charset="utf-8">
<title>yourCartly – Home</title>
<link rel="stylesheet" href="https://fonts.googleapis.com/css2?family=PT+Sans:wght@400;700&family=PT+Sans+Narrow:wght@400;700&display=swap">
<style>
:root{
  --black:#000;
  --strip:#6e6e6e;
  --page-bg:#d3d5d5;
  --panel:#efefef;
  --white:#fff;
  --red:#b8191c;
  --text:#1e1e1e;
  --muted:#bdbdbd;
  --orange:#f07a1c;
  --orange-dark:#e2541a;
  --line:#b5b5b5;
}
*{box-sizing:border-box;margin:0;padding:0}
html,body{width:1200px;height:1108px;overflow:hidden}
body{position:relative;background:var(--page-bg);font-family:"PT Sans",sans-serif;color:var(--text)}
.abs{position:absolute}
.top-strip{left:0;top:0;width:1200px;height:6px;background:var(--strip)}
.site-header{left:0;top:6px;width:1200px;height:145px;background:var(--black);border-bottom:3px solid var(--white)}
.brand{left:135px;top:2px;width:170px;height:143px;background:#0a0a0a;display:flex;align-items:flex-end;justify-content:center;padding-bottom:20px;gap:7px}
.brand-mark{width:12px;height:12px;background:var(--red);margin-bottom:5px}
.brand-name{font:700 24px "PT Sans",sans-serif;color:var(--white);letter-spacing:-.3px}
.search{left:824px;top:32px;width:202px;height:28px;border:1px solid #555;border-radius:5px;background:linear-gradient(#1c1c1c,#050505);color:#ddd;font-size:11px;padding:6px 10px}
.search-btn{position:absolute;right:6px;top:4px;width:18px;height:18px;border-radius:50%;background:#e8e8e8}
.nav{left:471px;top:93px;width:557px;height:31px;border:1px solid #666;border-radius:4px;background:linear-gradient(#2a2a2a,#060606);display:flex}
.nav a{color:var(--white);text-decoration:none;font-size:12.5px;display:flex;align-items:center;justify-content:center;border-right:1px solid #777}
.nav a:last-child{border-right:none}
.panel{left:154px;top:154px;width:892px;height:852px;background:var(--panel);box-shadow:0 0 8px rgba(0,0,0,.25)}
.hero{left:160px;top:154px;width:879px;height:407px;background:linear-gradient(100deg,#8c8f8f 0%,#c7c3bf 35%,#d6cfca 55%,#8ea7a3 80%,#b9bcbb 100%);box-shadow:0 2px 4px rgba(0,0,0,.35)}
.arrow{width:33px;height:33px;background:linear-gradient(#fff,#d8d8d8);border:1px solid #aaa;display:flex;align-items:center;justify-content:center}
.arrow.left{left:152px;top:344px;border-radius:4px 0 0 4px}
.arrow.right{left:1015px;top:344px;border-radius:0 4px 4px 0}
.title{font-family:"PT Sans Narrow",sans-serif;color:var(--red);font-size:20px}
.welcome-title{left:162px;top:577px}
.dots{left:164px;width:873px;border-top:1px dotted #333}
.intro{left:162px;top:620px;width:612px;font-size:12.4px;line-height:20.2px}
.intro-photo{left:789px;top:622px;width:246px;height:113px;background:linear-gradient(90deg,#d9dde0,#f0ede9 50%,#b9c7d6);border:1px solid #aaa}
.card{top:788px;height:207px;border:1px solid var(--line);padding:12px 13px}
.card.testimonial{left:165px;width:258px}
.card.newsletter{left:435px;width:258px}
.card.gallery{left:705px;width:329px;background:var(--white);border-color:#e2e2e2}
.card .title{display:block;border-bottom:1px solid var(--muted);padding-bottom:2px;margin-bottom:14px}
.entry{font-size:11.5px;line-height:15px;text-align:justify;padding-bottom:7px;margin-bottom:10px;border-bottom:1px solid var(--muted)}
.entry:last-child{border:none}
.entry time,.entry a{color:var(--red);display:block;text-decoration:none}
.entry a{padding-left:2px}
.field{height:28px;background:var(--white);border:1px solid #c4c4c4;font-size:11px;padding:7px 8px;margin:0 2px 6px 8px;width:236px}
.btn{display:inline-block;background:linear-gradient(var(--orange),var(--orange-dark));color:var(--white);font:12px "PT Sans Narrow",sans-serif;padding:5px 14px}
.signup{position:absolute;right:16px;top:136px}
.gallery-art{position:absolute;left:2px;top:60px;width:155px;height:125px;background:radial-gradient(circle at 50% 55%,#e4dccd 0,#eeeeee 45%,#fff 75%)}
.gallery-text{position:absolute;left:157px;top:62px;width:160px;font-size:12px;line-height:20px;text-align:justify}
.gallery .btn{position:absolute;left:157px;top:176px;padding:5px 6px}
.site-footer{left:0;top:1003px;width:1200px;height:105px;background:var(--black);border-top:3px solid var(--white);color:var(--white);font-size:12px;text-align:center;padding-top:48px}
</style>
</head>
<body>
<div class="abs top-strip"></div>
<header class="abs site-header">
  <div class="abs brand"><span class="brand-mark"></span><span class="brand-name">yourCartly</span></div>
  <div class="abs search">Search<span class="search-btn"></span></div>
  <nav class="abs nav">
    <a href="#" style="width:138px">yourCartly</a>
    <a href="#" style="width:137px">Gallery</a>
    <a href="#" style="width:126px">Contact Us</a>
    <a href="#" style="width:156px">Shopping Cart Payment</a>
  </nav>
</header>

<main>
  <div class="abs panel"></div>
  <div class="abs hero" role="img" aria-label="Photo of a child sitting in a supermarket shopping trolley full of groceries"></div>
  <div class="abs arrow left"><svg width="10" height="12" viewBox="0 0 10 12"><path d="M7 1 2 6l5 5" fill="none" stroke="#222" stroke-width="2"/></svg></div>
  <div class="abs arrow right"><svg width="10" height="12" viewBox="0 0 10 12"><path d="M3 1l5 5-5 5" fill="none" stroke="#222" stroke-width="2"/></svg></div>

  <h1 class="abs title welcome-title">welcome to our site</h1>
  <div class="abs dots" style="top:606px"></div>
  <p class="abs intro">yourCartlyevolved from demand!&nbsp; Apartment dwellers everywhere are calling for a solution to moving shopping, luggage and other goods from car to apartment, and vice versa. Other trolleys on the market are not versatile, they are not robust, but more importantly, they are NOT stylish! The emphasis of yourCartlyis on style. This trolley is stylish enough to remain in your apartment as a piece of furniture. It features a versatile flat-bed and hanger, to cope with all your transport needs. IT LOOKS GREAT!&nbsp; Designed along the lines of the familiar hotel “birdcage” luggage trolley...</p>
  <div class="abs intro-photo" role="img" aria-label="Photo of three people in a bright office meeting"></div>
  <div class="abs dots" style="top:766px"></div>

  <section class="abs card testimonial">
    <h2 class="title">Testimonial</h2>
    <div class="entry"><time>21.02.2012</time>Lorem Ipsum is simply dummy text of the printing and typesetting industry.<a href="#">Read More&gt;&gt;</a></div>
    <div class="entry"><time>21.02.2012</time>Lorem Ipsum is simply dummy text of the printing and typesetting industry.<a href="#">Read More&gt;&gt;</a></div>
  </section>

  <section class="abs card newsletter">
    <h2 class="title">Newsletter Signup</h2>
    <div class="field" style="margin-top:-1px">Enter your Name</div>
    <div class="field">Enter your Email id</div>
    <span class="btn signup">SIGN UP</span>
  </section>

  <section class="abs card gallery">
    <h2 class="title">photo gallery</h2>
    <div class="gallery-art" role="img" aria-label="Illustration of a figure pushing a hand trolley with boxes"></div>
    <p class="gallery-text">yourCartlyis made of high quality stainless steel and other robust materials. Whilst other trolleys tend to look like they belong in a factory</p>
    <span class="btn">Read More&gt;&gt;</span>
  </section>
</main>

<footer class="abs site-footer">Copyrights @ 2012 All Rights Reserved</footer>
</body>
</html>
```